Looking for a dynamic business card for a pizzeria.

A business card with our food, logo, and space for name, title, email, website, phone. The card should convey quality, unique, amazing. On the front, I envision food photo or photos with the owners names and contact information. On the back, more food with locations, website, facebook, twitter, instagram icons. It should look polished, not cartoonish, or plain.
Target Market(s)
upscale, local food buyers, 30-50 years in age.
Industry/Entity Type
Restaurant
Contact Information for Business Card
Business Name: Bru'nettix, LLC
Website: www.brunettix.com
Back:
2 locations: (can list on the back of card)
1. Marlow Point
4087 Corlan Avenue
Halden, WA 98031
360-481-5067
2. Crestwood Hill
7315 Wendmere Road
Halden, WA 98034
360-293-8840
front:
EDITABLE space for
Business name
Person's Name
title
2nd title
Email address
cell-phone number
Requirements
Must have
- logo
- my food photo or photos (no watermarks showing)
- locations on back
- Person contact information on front
- full bleed

```html
<!DOCTYPE html>
<html lang="en">
<head>
<meta charset="utf-8">
<title>Bru'nettix, LLC — Business Card</title>
<link rel="stylesheet" href="https://fonts.googleapis.com/css2?family=Open+Sans:wght@400;600;700&display=swap">
<style>
  :root {
    --bg: #ece8e3;
    --red: #b5192d;
    --red-light: #cf3a4c;
    --green: #1e5b2e;
    --white: #ffffff;
    --dough-light: #e6dccb;
    --dough-mid: #c9b99f;
    --dough-dark: #9e8d74;
    --ink-green: #1f5a2c;
  }
  * { box-sizing: border-box; margin: 0; padding: 0; }
  html, body { width: 1200px; height: 913px; overflow: hidden; }
  body {
    background: var(--bg);
    font-family: "Open Sans", Arial, sans-serif;
    position: relative;
  }
  .card {
    position: absolute;
    top: 302px;
    width: 540px;
    height: 309px;
    overflow: hidden;
    box-shadow: 0 6px 18px rgba(0,0,0,0.18);
  }
  .card--front { left: 40px; }
  .card--back { left: 620px; }
  .card__shapes { position: absolute; inset: 0; }

  .brand { position: absolute; display: flex; align-items: center; gap: 12px; }
  .brand__mark {
    width: 44px; height: 44px; border-radius: 50%;
    border: 3px solid var(--white);
  }
  .brand__name { color: var(--white); font-weight: 600; font-size: 30px; letter-spacing: 1px; }
  .company { position: absolute; color: var(--white); font-weight: 700; font-size: 22px; letter-spacing: 0.5px; }

  .card--front .brand { left: 34px; top: 48px; }
  .card--front .company { left: 58px; top: 110px; }

  .person { position: absolute; right: 34px; top: 38px; text-align: right; color: var(--white); }
  .person__name { font-weight: 700; font-size: 20px; letter-spacing: 0.5px; }
  .person__rule { height: 1px; background: var(--white); width: 170px; margin: 2px 0 3px auto; }
  .person__title { font-size: 12px; }

  .divider {
    position: absolute; left: 34px; top: 155px; width: 340px; height: 1px;
    background: rgba(255,255,255,0.8);
  }
  .contact { position: absolute; left: 34px; top: 166px; list-style: none; color: var(--white); font-size: 13.5px; line-height: 20px; }
  .contact li { display: flex; align-items: center; gap: 7px; }
  .contact svg { width: 11px; height: 11px; fill: none; stroke: var(--white); stroke-width: 1.6; }

  .food-photo {
    position: absolute; inset: 0;
    background:
      radial-gradient(ellipse 60% 45% at 30% 85%, var(--dough-mid), transparent 70%),
      radial-gradient(ellipse 45% 50% at 85% 25%, var(--dough-mid), transparent 70%),
      linear-gradient(160deg, var(--dough-light) 0%, var(--dough-mid) 55%, var(--dough-dark) 100%);
  }
  .card--back .brand { right: 40px; top: 36px; }
  .card--back .brand__name { font-size: 26px; }
  .card--back .company { right: 40px; top: 90px; font-size: 20px; }

  .locations { position: absolute; left: 40px; top: 150px; color: var(--ink-green); font-weight: 600; font-size: 13px; line-height: 17px; }
  .location + .location { margin-top: 8px; }
</style>
</head>
<body>

  <section class="card card--front" aria-label="Business card front">
    <svg class="card__shapes" viewBox="0 0 540 309" preserveAspectRatio="none" aria-hidden="true">
      <defs>
        <linearGradient id="redFill" x1="0" y1="0" x2="0.4" y2="1">
          <stop offset="0" stop-color="var(--red-light)"/>
          <stop offset="1" stop-color="var(--red)"/>
        </linearGradient>
      </defs>
      <rect width="540" height="309" fill="url(#redFill)"/>
      <rect x="0" y="284" width="540" height="25" fill="var(--green)"/>
      <path d="M372 284 Q376 268 382 258 Q392 236 420 236 L540 236 L540 284 Z" fill="var(--white)"/>
    </svg>

    <div class="brand">
      <span class="brand__mark"></span>
      <span class="brand__name">BRU'NETTIX</span>
    </div>
    <div class="company">BRU'NETTIX, LLC</div>

    <div class="person">
      <div class="person__name">MARCO DELVANE</div>
      <div class="person__rule"></div>
      <div class="person__title">Director, President</div>
    </div>

    <div class="divider"></div>
    <ul class="contact">
      <li><svg viewBox="0 0 12 12"><path d="M3 1 L5 3.5 L4 5 Q5 7 7 8 L8.5 7 L11 9 L9.5 11 Q4 10.5 1 2.5 Z"/></svg>360-518-2704</li>
      <li><svg viewBox="0 0 12 12"><rect x="1" y="2.5" width="10" height="7"/><path d="M1 2.5 L6 6.5 L11 2.5"/></svg>info@marcodelvane.com</li>
      <li><svg viewBox="0 0 12 12"><circle cx="6" cy="6" r="5"/><path d="M1 6 H11 M6 1 Q3 6 6 11 Q9 6 6 1"/></svg>www.brunettix.com</li>
    </ul>
  </section>

  <section class="card card--back" aria-label="Business card back">
    <div class="food-photo" role="img" aria-label="Close-up photo of rounds of pizza dough"></div>
    <svg class="card__shapes" viewBox="0 0 540 309" preserveAspectRatio="none" aria-hidden="true">
      <rect x="250" y="286" width="290" height="23" fill="var(--green)"/>
      <path d="M0 309 L0 288 L225 288 Q248 288 256 270 Q262 258 280 256 L280 309 Z" fill="var(--red)"/>
    </svg>

    <div class="brand">
      <span class="brand__mark"></span>
      <span class="brand__name">BRU'NETTIX</span>
    </div>
    <div class="company">BRU'NETTIX, LLC</div>

    <div class="locations">
      <p class="location">360-481-5067<br>Marlow Point 4087 Corlan Avenue<br>Halden, WA 98031</p>
      <p class="location">360-293-8840<br>Crestwood Hill 7315 Wendmere Road<br>Halden, WA 98034</p>
    </div>
  </section>

</body>
</html>
```